Local Roofing/Construction company business needs new biz card design

We need a new business card design, current cards are from the start of this operation and generic at best. We are a local Construction Company (General Contractor) with a majority of our work originating from insurance claims-exterior finish work is the main focus (Roofs-Siding-Gutters etc). Heavily involved with homeowners and the low ball offers they receive from insurance company's after a insurable event takes place. I have attached some of our original logo file(s) below.

```html
<!DOCTYPE html>
<html lang="en">
<head>
<meta charset="utf-8">
<title>T-Forge Construction – Business Card</title>
<link href="https://fonts.googleapis.com/css2?family=Montserrat:wght@400;500;700;800&display=swap" rel="stylesheet">
<style>
  :root {
    --stage: #1c1d21;
    --brand-green: #3fb865;
    --pattern-green: #4fc074;
    --pattern-deep: #38a95b;
    --ink-dark: #0f1f24;
    --paper: #f8f5f2;
    --white: #ffffff;
    --muted: #dfe6e6;
  }
  * { box-sizing: border-box; margin: 0; padding: 0; }
  html, body {
    width: 1200px; height: 900px; overflow: hidden;
    background: var(--stage);
    font-family: "Montserrat", sans-serif;
  }
  .card {
    position: absolute; left: 250px;
    width: 700px; height: 400px;
    border-radius: 26px; overflow: hidden;
    box-shadow: 0 18px 40px rgba(0,0,0,.45);
  }
  /* ---- front ---- */
  .card--front { top: 40px; }
  .front-pattern {
    position: absolute; inset: 0;
    background: linear-gradient(135deg, var(--pattern-green), var(--pattern-deep));
  }
  .front-badge {
    position: absolute; left: 50%; top: 50%;
    width: 230px; height: 170px; transform: translate(-50%, -50%);
    background: var(--white); border-radius: 22px;
    display: flex; flex-direction: column; align-items: center; justify-content: center;
    color: var(--brand-green); font-weight: 800; text-align: center; line-height: 1.05;
  }
  .front-badge .wordmark-main { font-size: 34px; letter-spacing: 1px; }
  .front-badge .wordmark-sub { font-size: 15px; letter-spacing: 2px; margin-top: 4px; }
  /* ---- back ---- */
  .card--back { top: 470px; background: var(--paper); }
  .back-shapes { position: absolute; inset: 0; }
  .back-brand {
    position: absolute; left: 44px; top: 56px;
    display: flex; align-items: center; gap: 12px;
  }
  .back-brand .brand-mark { width: 34px; height: 34px; background: var(--brand-green); }
  .back-brand .wordmark { color: var(--ink-dark); font-weight: 800; line-height: 1; }
  .back-brand .wordmark-main { font-size: 30px; letter-spacing: 1px; display: block; }
  .back-brand .wordmark-sub { font-size: 12.5px; letter-spacing: 2.6px; display: block; margin-top: 3px; }
  .contact {
    position: absolute; right: 40px; top: 150px;
    text-align: right; color: var(--white);
  }
  .contact-name { color: var(--brand-green); font-weight: 700; font-size: 26px; line-height: 1.2; }
  .contact-role { font-size: 14px; color: var(--muted); margin-top: 2px; margin-bottom: 14px; }
  .contact-address { font-size: 14px; line-height: 1.4; margin-bottom: 8px; }
  .contact-line {
    display: flex; justify-content: flex-end; align-items: center; gap: 10px;
    font-size: 14px; line-height: 1.6;
  }
  .contact-icon { width: 13px; height: 13px; fill: var(--brand-green); flex: none; }
</style>
</head>
<body>

<section class="card card--front">
  <div class="front-pattern" role="img" aria-label="Repeating company wordmark pattern in green"></div>
  <div class="front-badge">
    <span class="wordmark-main">T-FORGE</span>
    <span class="wordmark-sub">CONSTRUCTION</span>
  </div>
</section>

<section class="card card--back">
  <svg class="back-shapes" viewBox="0 0 700 400" width="700" height="400" aria-hidden="true">
    <path d="M485 0 C385 30 400 300 70 362 L0 372 L0 400 L700 400 L700 0 Z" fill="var(--ink-dark)"/>
    <path d="M478 8 C388 45 398 302 76 352 L0 362" fill="none" stroke="var(--white)" stroke-width="2.5"/>
    <path d="M700 14 C590 20 500 58 446 150 C510 88 600 56 700 44 Z" fill="var(--brand-green)"/>
  </svg>

  <div class="back-brand">
    <span class="brand-mark"></span>
    <span class="wordmark">
      <span class="wordmark-main">T-FORGE</span>
      <span class="wordmark-sub">CONSTRUCTION</span>
    </span>
  </div>

  <div class="contact">
    <p class="contact-name">Daniel Moreau</p>
    <p class="contact-role">Owner</p>
    <p class="contact-address">418 Maple Grove Ave, #112<br>Fairmont, OH 43190</p>
    <p class="contact-line">877-555-0142
      <svg class="contact-icon" viewBox="0 0 16 16"><path d="M3 1h3l1.5 4-2 1.2a9 9 0 0 0 4.3 4.3L11 8.5l4 1.5v3a2 2 0 0 1-2 2A13 13 0 0 1 1 3a2 2 0 0 1 2-2z"/></svg></p>
    <p class="contact-line">877-555-0187
      <svg class="contact-icon" viewBox="0 0 16 16"><path d="M4 0h8a1 1 0 0 1 1 1v14a1 1 0 0 1-1 1H4a1 1 0 0 1-1-1V1a1 1 0 0 1 1-1zm1 2v10h6V2z"/></svg></p>
    <p class="contact-line">info@t-forgeconstruction.com
      <svg class="contact-icon" viewBox="0 0 16 16"><path d="M1 3h14v10H1z M1 3l7 6 7-6"/></svg></p>
    <p class="contact-line">www.t-forgeconstruction.com
      <svg class="contact-icon" viewBox="0 0 16 16"><circle cx="8" cy="8" r="7"/></svg></p>
  </div>
</section>

</body>
</html>
```